Business Card Design Project - 2 sided

We need a business card design for a card having one business on each side (ie. two businesses on one card). Would like a design that incorporates logo, tagline and normal fields (name, position, address, phone).

Would also like an allowance for small font text along the bottom (text to be determined, but less than 50 characters).

NB. Attached logo for Harbor Quill has two variations - either can be used.

www.harborquill-example.com / www.velmaro-example.com

```html
<!DOCTYPE html>
<html lang="en">
<head>
<meta charset="utf-8">
<title>Two-sided business card – Harbor Quill / Velmaro</title>
<link rel="stylesheet" href="https://fonts.googleapis.com/css2?family=Tinos:wght@400;700&family=Questrial&display=swap">
<style>
  :root {
    --page-bg: #e8e5e0;
    --card-bg: #ffffff;
    --card-tint: #f1f1f1;
    --green: #8cc63f;
    --green-dark: #6aa52a;
    --navy: #2d2a78;
    --blue: #2a8fd0;
    --ink: #3d3d3d;
    --ink-soft: #6b6b6b;
    --photo-light: #e9e4df;
    --photo-mid: #9c8f86;
    --photo-dark: #2f3340;
  }
  * { box-sizing: border-box; margin: 0; padding: 0; }
  html, body { width: 1200px; height: 900px; overflow: hidden; }
  body { background: var(--page-bg); position: relative; }

  .card {
    position: absolute;
    left: 290px;
    width: 620px;
    height: 354px;
    background: var(--card-bg);
    overflow: hidden;
    box-shadow: 0 6px 18px rgba(0,0,0,.18);
  }
  .card--front { top: 70px; font-family: "Tinos", "Times New Roman", serif; color: var(--ink); background: linear-gradient(180deg, var(--card-bg) 0%, var(--card-tint) 100%); }
  .card--back { top: 476px; font-family: "Questrial", Arial, sans-serif; color: var(--ink); }

  /* ---------- Harbor Quill side ---------- */
  .front-topline { position: absolute; left: 250px; right: 0; top: 0; height: 6px; background: var(--green-dark); }
  .front-nameband {
    position: absolute; left: 210px; right: 0; top: 22px; height: 36px;
    background: var(--green);
    clip-path: polygon(18px 0, 100% 0, 100% 100%, 0 100%);
    display: flex; align-items: center; padding-left: 40px; gap: 10px;
  }
  .front-nameband .person-name { font-size: 21px; font-weight: 700; color: var(--navy); }
  .front-nameband .person-role { font-size: 13px; color: var(--navy); }
  .front-photo {
    position: absolute; left: 370px; right: 0; top: 58px; height: 240px;
    background: linear-gradient(160deg, var(--photo-light) 0%, var(--photo-mid) 55%, var(--photo-dark) 100%);
  }
  .front-footband {
    position: absolute; left: 280px; right: 0; top: 298px; height: 18px;
    background: var(--navy);
    clip-path: polygon(24px 0, 100% 0, 100% 100%, 0 100%);
  }
  .front-brand { position: absolute; left: 32px; top: 84px; display: flex; align-items: center; gap: 12px; }
  .brand-dot { width: 34px; height: 34px; border-radius: 50%; background: var(--green); }
  .front-brand .brand-name { font-size: 28px; color: var(--navy); letter-spacing: .5px; }
  .front-tagline { position: absolute; left: 78px; top: 124px; font-size: 12px; color: var(--ink-soft); }
  .front-rule { position: absolute; left: 78px; top: 144px; width: 200px; border-top: 1px dotted var(--ink-soft); }
  .front-address { position: absolute; left: 78px; top: 158px; font-size: 14px; line-height: 18px; }
  .contact-list { list-style: none; }
  .front-contacts { position: absolute; left: 78px; top: 200px; font-size: 13px; line-height: 18px; }
  .contact-list li { display: flex; align-items: center; gap: 7px; }
  .contact-icon { width: 11px; height: 11px; flex: none; }
  .front-note { position: absolute; left: 78px; top: 262px; width: 270px; font-size: 9px; line-height: 11px; color: var(--ink-soft); }

  /* ---------- Velmaro side ---------- */
  .back-photo {
    position: absolute; left: 360px; right: 0; top: 0; height: 236px;
    background: linear-gradient(200deg, var(--photo-light) 0%, var(--photo-mid) 50%, var(--photo-dark) 100%);
  }
  .back-sideband { position: absolute; left: 360px; right: 0; top: 236px; height: 12px; background: var(--green); }
  .back-footband { position: absolute; left: 0; right: 0; bottom: 0; height: 12px; background: var(--green); }
  .back-brand { position: absolute; left: 32px; top: 34px; display: flex; align-items: center; gap: 12px; }
  .back-brand .brand-name { font-size: 40px; color: var(--blue); }
  .back-tagline { position: absolute; left: 80px; top: 88px; font-size: 12px; color: var(--green-dark); }
  .back-rule { position: absolute; left: 80px; top: 106px; width: 210px; border-top: 1px dotted var(--green-dark); }
  .back-name { position: absolute; left: 80px; top: 118px; font-size: 20px; color: var(--blue); }
  .back-role { position: absolute; left: 80px; top: 142px; font-size: 13px; color: var(--ink); }
  .back-contacts { position: absolute; left: 80px; top: 170px; font-size: 14px; line-height: 19px; }
  .back-address { position: absolute; left: 370px; top: 262px; font-size: 11px; line-height: 14px; }
  .back-note { position: absolute; left: 80px; top: 292px; width: 270px; font-size: 9px; line-height: 11px; color: var(--ink-soft); }
</style>
</head>
<body>

<section class="card card--front" aria-label="Harbor Quill side">
  <div class="front-topline"></div>
  <div class="front-nameband">
    <span class="person-name">Dana Whitfield</span>
    <span class="person-role">Manager</span>
  </div>
  <div class="front-photo" role="img" aria-label="Photo of a smiling group of business people in suits"></div>
  <div class="front-footband"></div>

  <div class="front-brand">
    <span class="brand-dot"></span>
    <span class="brand-name">Harbor Quill</span>
  </div>
  <p class="front-tagline">tagline</p>
  <div class="front-rule"></div>
  <p class="front-address">42 Lantern Street<br>Eastvale VIC 3999, AUSTRALIA</p>
  <ul class="contact-list front-contacts">
    <li><svg class="contact-icon" viewBox="0 0 12 12"><path d="M2.5 1h2l1 3-1.5 1a7 7 0 0 0 3 3l1-1.5 3 1v2a1 1 0 0 1-1 1A10 10 0 0 1 1.5 2a1 1 0 0 1 1-1z" fill="var(--navy)"/></svg>+61 3 5550 0142</li>
    <li><svg class="contact-icon" viewBox="0 0 12 12"><rect x="1" y="2.5" width="10" height="7" fill="var(--navy)"/><path d="M1 2.5l5 4 5-4" stroke="#fff" fill="none"/></svg>info@harborquill-example.com</li>
    <li><svg class="contact-icon" viewBox="0 0 12 12"><rect x="1" y="1" width="10" height="10" fill="var(--navy)"/><circle cx="6" cy="6" r="3" stroke="#fff" fill="none"/></svg>www.harborquill-example.com</li>
  </ul>
  <p class="front-note">Clear words, careful service and friendly people ready to help your business every day.</p>
</section>

<section class="card card--back" aria-label="Velmaro side">
  <div class="back-photo" role="img" aria-label="Photo of a smiling businesswoman giving a thumbs up"></div>
  <div class="back-sideband"></div>
  <div class="back-footband"></div>

  <div class="back-brand">
    <span class="brand-dot"></span>
    <span class="brand-name">Velmaro</span>
  </div>
  <p class="back-tagline">tagline</p>
  <div class="back-rule"></div>
  <p class="back-name">Dana Whitfield</p>
  <p class="back-role">Manager</p>
  <ul class="contact-list back-contacts">
    <li><svg class="contact-icon" viewBox="0 0 12 12"><path d="M2.5 1h2l1 3-1.5 1a7 7 0 0 0 3 3l1-1.5 3 1v2a1 1 0 0 1-1 1A10 10 0 0 1 1.5 2a1 1 0 0 1 1-1z" fill="var(--blue)"/></svg>+1 555-014-0192</li>
    <li><svg class="contact-icon" viewBox="0 0 12 12"><rect x="1" y="2.5" width="10" height="7" fill="var(--blue)"/><path d="M1 2.5l5 4 5-4" stroke="#fff" fill="none"/></svg>support@velmaro-example.com</li>
    <li><svg class="contact-icon" viewBox="0 0 12 12"><rect x="1" y="1" width="10" height="10" fill="var(--blue)"/><circle cx="6" cy="6" r="3" stroke="#fff" fill="none"/></svg>www.velmaro-example.com</li>
  </ul>
  <p class="back-address">PO Box 27<br>Ridgefield Missouri 63000, USA<br>118 Marlow Drive<br>Bayview, Florida 34000, USA</p>
  <p class="back-note">Clear words, careful service and friendly people ready to help your business every day.</p>
</section>

</body>
</html>
```